Bluefern Business Services needs a new interactive and interesting website

We need an interesting, professional, modern and functional company website for Bluefern Business Services - a young IT Services company based out of Chennai, India.

Bluefern Business Services is a fully owned subsidiary of Marlow Goods, one of the world's leading direct to consumer wine merchant.

We already have a registered company logo which must feature in the website.

We conceive, design, develop, test, implement and support IT solutions across the entire Marlow Goods IT landscape. For ex : We currently run about 25 e-commerce websites for Marlow Goods on ATG and Dot Net.

We would like to see our corporate colors used in the website. (Burgundy wine and wine green - source: www.bluefernbs-site.com)

We are looking at this website to communicate a fun, friendly and professionally managed company - reaching out to career seekers, prospective customers and general public.

For reference - The company name 'Bluefern' is an inspiration from the Marlow Goods lineage.

The second image with the world map is stickered on our main entrance to the office, I am not sure where this can be used -just putting it out there..

Please note that there are only a few more days to submit designs for this contest  !

I would appreciate if you can help posting your designs in time for our review and consideration.

Thanks.

Reason: Thanks for your inputs. We have a number of designers and a lot to digest and work with in the past few days. There has been a rush of new designs in the last few days Hence we will require more time to process these and make our decision. Hence i am requesting the contest to be open for more days. Regards, Tarun

Target Market(s)

Prospective job seekers who want to know more about the company and also wish to apply for a job vacancy
People wanting to know more about the company in general and our progress
People who want to see what we offer and how we can help them too - prospective customers
Companies that are interested in our IT Captive journey and are looking for a business opportunity

Industry/Entity Type

E-Commerce

Requirements
Must have
• Log In/ Register facility acting as a Single Sign on for Intranet (Employees)

Facility to post job vacancies (with an expiry date) and enable people to apply for a role and upload their CV/Resume.

Facility to Review Job applications

Facility for website visitors to contact Bluefern business Services via an online 'Contact Us' form with a split of job seekers and business opportunities

Gallery facility to upload pictures regarding company events
Nice to have
• Less Cluttered and contemporary design
Some Wine/Vineyard inspirations will be good but not too much, the company is an IT services company

```html
<!DOCTYPE html>
<html lang="en">
<head>
<meta charset="utf-8">
<title>Bluefern Business Services</title>
<link href="https://fonts.googleapis.com/css2?family=Open+Sans:ital,wght@0,300;0,400;0,600;0,700;1,400&display=swap" rel="stylesheet">
<style>
:root{
  --burgundy:#880041;
  --olive:#7f8a2f;
  --olive-band:#8b913f;
  --text:#555;
  --dark:#333;
  --line:#dcdcdc;
  --card:#efefef;
}
*{box-sizing:border-box;margin:0;padding:0}
html,body{width:1029px;height:1200px;overflow:hidden;background:#fff}
body{font-family:"Open Sans",sans-serif;color:var(--text)}
.page{position:relative;width:1200px;height:1400px;transform:scale(0.8575);transform-origin:0 0;background:#fff}
.abs{position:absolute}

.site-header{left:0;top:0;width:1200px;height:103px;background:var(--burgundy);border-bottom:3px solid var(--olive)}
.brand{left:130px;top:20px;display:flex;align-items:center;gap:10px;color:#fff}
.brand-dot{width:26px;height:26px;border-radius:50%;background:#fff}
.brand-name{font-weight:600;font-size:30px;line-height:32px}
.brand-name small{display:block;font-size:21px;line-height:26px;font-weight:600}
.search{left:850px;top:40px;width:220px;height:35px;display:flex}
.search-field{flex:1;background:#fff;font-style:italic;font-size:13px;color:#888;padding:9px 14px}
.search-btn{width:35px;background:var(--olive);display:flex;align-items:center;justify-content:center}

.main-nav{right:130px;top:104px;display:flex;height:40px}
.main-nav a{font-size:13.5px;color:var(--dark);text-decoration:none;padding:0 15px;line-height:42px;text-transform:uppercase}
.main-nav a.active{background:var(--olive);color:#fff;padding:0 13px}

.hero{left:130px;top:149px;width:940px;height:389px;border:5px solid var(--line);background:#fff}
.hero-photo{position:absolute;right:0;top:0;width:600px;height:379px;background:linear-gradient(90deg,#fff 0%,#e9e9e9 25%,#cfcfd2 60%,#b9b9bd 100%)}
.hero-title{position:absolute;left:20px;top:90px;font-size:37px;font-weight:600;color:var(--burgundy)}
.hero-title span{color:var(--olive)}
.hero-text{position:absolute;left:23px;top:141px;width:370px;font-size:15.5px;line-height:22px;color:var(--dark)}
.dots{position:absolute;left:22px;top:345px;display:flex;gap:7px}
.dots i{width:17px;height:17px;border-radius:50%;background:#a8a8a8}
.dots i.on{background:var(--olive)}

h2{font-weight:400;font-size:24px;color:var(--burgundy)}
.welcome{left:130px;top:563px;width:515px}
.welcome-photo{position:absolute;left:0;top:49px;width:202px;height:138px;background:linear-gradient(135deg,#c9d4de,#8fa0b3)}
.welcome p{position:absolute;left:220px;top:43px;width:295px;font-size:13.5px;line-height:23px}
.divider-v{left:663px;top:570px;width:1px;height:195px;background:var(--line)}
.services{left:691px;top:563px;width:380px}
.services p{margin-top:16px;font-size:13.5px;line-height:23px}
.services ul{list-style:none;margin-top:9px}
.services li{display:flex;align-items:center;gap:8px;font-size:13.5px;color:var(--olive);height:28px}
.rule{left:130px;top:795px;width:940px;height:1px;background:var(--line)}

.events{left:130px;top:814px;width:606px;height:297px;border:1px solid var(--line);background:linear-gradient(#efefef,#fff 60%)}
.events h2{position:absolute;left:19px;top:15px}
.events-arrows{position:absolute;left:550px;top:25px;display:flex;gap:10px}
.event{position:absolute;left:21px;width:565px;display:flex;gap:18px}
.event-photo{flex:none;width:102px;height:89px;background:linear-gradient(135deg,#3a4f8c,#15203f)}
.event-photo.expo{background:linear-gradient(135deg,#d8d2cb,#8c2f2a)}
.event h3{font-weight:400;font-size:14.5px;line-height:20px;color:var(--olive)}
.event p{margin-top:4px;font-size:13px;line-height:20px}
.event p em{color:var(--burgundy)}
.event-sep{position:absolute;left:21px;top:162px;width:565px;height:1px;background:#e0e0e0}

.opps{left:768px;top:806px;width:302px}
.opp{position:absolute;left:2px;width:300px;height:124px;background:var(--card);padding:14px 14px;font-size:13px;line-height:18px}
.opp b{font-weight:600;color:var(--dark)}
.opp .date{display:block;margin-top:3px;font-weight:600;color:var(--burgundy)}

.clients{left:0;top:1132px;width:1200px;height:151px;background:#fff;box-shadow:0 -6px 8px -6px rgba(0,0,0,.08)}
.clients h2{text-align:center;margin-top:20px}
.client-row{display:flex;justify-content:space-between;align-items:center;width:940px;margin:22px auto 0}
.client{width:140px;text-align:center;font-size:19px;font-weight:600;color:#8a8a8a;line-height:22px}

.site-footer{left:0;top:1283px;width:1200px;height:117px;background:var(--olive-band);color:#fff}
.foot-links{position:absolute;left:130px;top:20px;font-size:14.5px}
.foot-links span{margin:0 14px;opacity:.8}
.copy{position:absolute;left:130px;top:63px;font-size:12px;line-height:19px}
.copy em{font-style:normal;color:var(--burgundy)}
.social{position:absolute;left:894px;top:25px;display:flex;gap:7px}
.social i{width:30px;height:30px;border-radius:3px;background:#e9ecef;border:1px solid rgba(0,0,0,.15)}
</style>
</head>
<body>
<div class="page">
  <header class="site-header abs">
    <div class="brand abs" style="left:130px;top:20px;position:absolute">
      <span class="brand-dot"></span>
      <div class="brand-name">Bluefern<small>Business Services</small></div>
    </div>
    <div class="search abs">
      <div class="search-field">Search...</div>
      <div class="search-btn">
        <svg width="20" height="20" viewBox="0 0 20 20"><circle cx="8" cy="8" r="5.5" fill="none" stroke="#fff" stroke-width="2.5"/><path d="M12 12l6 6" stroke="#fff" stroke-width="3" stroke-linecap="round"/></svg>
      </div>
    </div>
  </header>

  <nav class="main-nav abs">
    <a class="active">Home</a><a>About Us</a><a>Clients</a><a>Services</a><a>Careers</a><a>Contact Us</a>
  </nav>

  <section class="hero abs">
    <div class="hero-photo" role="img" aria-label="Photo of a smiling business team gathered around a laptop"></div>
    <h1 class="hero-title">Delivering <span>IT</span> Excellence</h1>
    <p class="hero-text">Bluefern Business Services' vision is to deliver outstanding technology solutions to all of the Marlow Goods' group companies...</p>
    <div class="dots"><i class="on"></i><i></i><i></i><i></i></div>
  </section>

  <section class="welcome abs">
    <h2>Welcome to Our Website</h2>
    <div class="welcome-photo" role="img" aria-label="Photo of a man holding a laptop in an office"></div>
    <p>Welcome to Bluefern Business Services, an emerging provider of global IT consulting and software services. We are part of the Marlow Goods group, a family run business and the world's largest multi-channel home delivery wine merchant.</p>
  </section>
  <div class="divider-v abs"></div>
  <section class="services abs">
    <h2>Our Services</h2>
    <p>The services we provide enable the businesses we support to efficiently manage key functions...</p>
    <ul>
      <li><svg width="13" height="11" viewBox="0 0 13 11"><path d="M1 6l3.5 3.5L12 1" fill="none" stroke="#880041" stroke-width="2.5"/></svg>Packaged Applications</li>
      <li><svg width="13" height="11" viewBox="0 0 13 11"><path d="M1 6l3.5 3.5L12 1" fill="none" stroke="#880041" stroke-width="2.5"/></svg>Enterprise Application Integration</li>
      <li><svg width="13" height="11" viewBox="0 0 13 11"><path d="M1 6l3.5 3.5L12 1" fill="none" stroke="#880041" stroke-width="2.5"/></svg>Digital Commerce</li>
      <li><svg width="13" height="11" viewBox="0 0 13 11"><path d="M1 6l3.5 3.5L12 1" fill="none" stroke="#880041" stroke-width="2.5"/></svg>Application Development &amp; Maintenance</li>
    </ul>
  </section>
  <div class="rule abs"></div>

  <section class="events abs">
    <h2>Latest Events</h2>
    <div class="events-arrows">
      <svg width="14" height="18" viewBox="0 0 14 18"><path d="M10 2L3 9l7 7" fill="none" stroke="#555" stroke-width="2"/></svg>
      <svg width="14" height="18" viewBox="0 0 14 18"><path d="M4 2l7 7-7 7" fill="none" stroke="#555" stroke-width="2"/></svg>
    </div>
    <article class="event" style="top:58px">
      <div class="event-photo" role="img" aria-label="Photo of an audience at a conference presentation"></div>
      <div><h3>Aliquam molestie, mi et imperdiet euismod, dui purus auctor tellus..</h3>
      <p>Et interdum lacus lectus et ante. Sed accumsan sollicitudin sapien, sit amet adipiscing turpis gravida ac....<em>Read More</em></p></div>
    </article>
    <div class="event-sep"></div>
    <article class="event" style="top:176px">
      <div class="event-photo expo" role="img" aria-label="Photo of visitors at an exhibition stand"></div>
      <div><h3>Aliquam molestie, mi et imperdiet euismod, dui purus auctor tellus..</h3>
      <p>Et interdum lacus lectus et ante. Sed accumsan sollicitudin sapien, sit amet adipiscing turpis gravida ac....<em>Read More</em></p></div>
    </article>
  </section>

  <section class="opps abs">
    <h2>Latest Opportunities</h2>
    <div class="opp" style="top:42px"><b>Software Developers/Programmer Analysts - AX</b><br>We are looking for a AX Software Developer to join...<span class="date">26/11/2013</span></div>
    <div class="opp" style="top:181px"><b>Software Developers/Programmer Analysts - AX</b><br>We are looking for a AX Software Developer to join...<span class="date">26/11/2013</span></div>
  </section>

  <section class="clients abs">
    <h2>Our Clients</h2>
    <div class="client-row">
      <div class="client">Kestrel Wine<br><span style="font-size:12px">The Morning Ledger</span></div>
      <div class="client">Harrowgate</div>
      <div class="client">Penwick</div>
      <div class="client">Maison Vigne</div>
      <div class="client">Marlow Goods</div>
      <div class="client" style="font-size:15px;line-height:18px">The Weekend Cellar Club</div>
    </div>
  </section>

  <footer class="site-footer abs">
    <div class="foot-links">Home<span>|</span>About us<span>|</span>Careers<span>|</span>Services<span>|</span>Clients<span>|</span>Contact Us</div>
    <div class="copy">Copyright © 2014. <em>Bluefern Business Services Private Limited.</em><br>All Right Reserved</div>
    <div class="social" aria-label="Social links"><i></i><i></i><i></i><i></i><i></i></div>
  </footer>
</div>
</body>
</html>
```